Bootcamp Bikini Summer body 12 week challenge Flyer/Advertising

I require a 12 week summer challenge flyer/advertisements, of various sizes- A4, website banner, square instagram type.

The Details that must be on the advertisements:

Clara Vantrell presents the 'Get Summer ready' with her very own personalised programming to get you ultimate beach body- ready before Summer hits!
ONLY $59.95 per week
Includes:
-Customised meal plan (usually $220)
-Weekly weigh in/check ins with Clara!
-3 weekly training sessions, with different training style to ensure your body is always left guessing, in a fun team environment. Run by one of Clara's very own trainers, from Keep the pace training facility!
-Discounted additional PT sessions.
-Qualified, experienced and result driven trainers
-Proven results with thousands of women, worldwide
-Prize pack for the challenge winner
-The best beach body ready for Summer!
SECURE YOUR PLACE NOW AS PLACES ARE CAPPED:
contact@claravantrell.com.au or text 0491 503 617 to sign up NOW
(smaller writing)
t&c -Full 12 weeks must be paid for, even if sessions are missed or cancelled. Weekly deductions must be set up upon confirmation using a credit card, with the first 2 weeks deducted up front, the remaining 10 weeks will be deducted weekly.

```html
<!DOCTYPE html>
<html lang="en">
<head>
<meta charset="utf-8">
<title>Get Summer Ready – Clara Vantrell</title>
<link rel="stylesheet" href="https://fonts.googleapis.com/css2?family=Arimo:ital,wght@0,400;0,700;1,700&display=swap">
<style>
  :root {
    --bg-light: #fbe0ec;
    --bg-mid: #f5c3d9;
    --brand-pink: #e8388e;
    --band-pink: #e1468f;
    --text-grey: #545454;
    --text-dark: #2b2b2b;
    --yellow: #fcc20f;
    --yellow-deep: #f6ae00;
    --white: #ffffff;
  }
  * { margin: 0; padding: 0; box-sizing: border-box; }
  html, body { width: 849px; height: 1200px; overflow: hidden; }
  body { font-family: "Arimo", Arial, sans-serif; color: var(--text-grey); }

  .flyer {
    position: relative;
    width: 849px;
    height: 1200px;
    overflow: hidden;
    background: radial-gradient(ellipse at 60% 35%, var(--bg-light) 0%, var(--bg-mid) 75%);
  }
  .bokeh { position: absolute; border-radius: 50%; background: rgba(255,255,255,0.28); }

  .hero-photo {
    position: absolute;
    left: 428px; top: 0;
    width: 421px; height: 1056px;
    background: linear-gradient(180deg, #5a3a30 0%, #a0715a 30%, #b8856a 55%, #8b8d94 75%, #6f6f76 100%);
    border-radius: 40% 30% 0 0 / 8% 6% 0 0;
    opacity: 0.9;
  }

  .brand-box {
    position: absolute;
    left: 64px; top: 71px;
    width: 229px; height: 57px;
    background: var(--white);
    display: flex; align-items: center; justify-content: center;
  }
  .brand-name { font-weight: 700; font-size: 26px; color: var(--brand-pink); }

  .presents { position: absolute; left: 66px; top: 134px; font-size: 19px; font-weight: 700; }

  .headline {
    position: absolute;
    left: 60px; top: 170px;
    font-size: 76px; line-height: 78px;
    font-style: italic; font-weight: 700;
    color: var(--brand-pink);
    letter-spacing: -2px;
  }

  .intro {
    position: absolute;
    left: 64px; top: 452px;
    width: 380px;
    font-size: 21px; line-height: 24px;
  }

  .price-badge {
    position: absolute;
    left: 364px; top: 497px;
    width: 128px; height: 128px;
    border-radius: 50%;
    background: radial-gradient(circle at 40% 35%, var(--yellow) 55%, var(--yellow-deep) 100%);
    box-shadow: 0 3px 8px rgba(0,0,0,0.2);
    display: flex; flex-direction: column; align-items: center; justify-content: center;
    color: var(--text-dark); font-weight: 700; line-height: 1;
  }
  .price-badge .only { font-size: 17px; }
  .price-badge .amount { font-size: 29px; font-style: italic; margin: 2px 0; }
  .price-badge .per { font-size: 16px; }

  .includes { position: absolute; left: 64px; top: 648px; width: 420px; }
  .includes h2 { font-size: 27px; color: var(--text-dark); margin-bottom: 6px; }
  .includes ul { list-style: none; }
  .includes li {
    position: relative;
    padding-left: 12px;
    font-size: 15.5px; line-height: 18px;
    margin-bottom: 8px;
    color: var(--text-dark);
  }
  .includes li::before { content: "•"; position: absolute; left: 0; }

  .start-badge {
    position: absolute;
    left: 534px; top: 819px;
    width: 274px; height: 274px;
    border-radius: 50%;
    background: var(--white);
    box-shadow: 0 4px 14px rgba(0,0,0,0.15);
  }
  .start-badge-inner {
    position: absolute;
    left: 14px; top: 14px;
    width: 246px; height: 246px;
    border-radius: 50%;
    background: var(--yellow);
    display: flex; align-items: center; justify-content: center;
    text-align: center;
    font-size: 34px; line-height: 36px;
    color: var(--text-dark);
  }
  .start-badge-inner strong { font-weight: 700; letter-spacing: -1px; }

  .footer-band { position: absolute; left: 0; top: 1030px; width: 849px; height: 170px; }
  .footer-text { position: absolute; left: 82px; top: 1088px; color: var(--white); }
  .footer-cta { font-size: 20px; line-height: 26px; }
  .terms { margin-top: 20px; font-size: 7.5px; line-height: 10px; width: 600px; opacity: 0.9; }
</style>
</head>
<body>
<div class="flyer">
  <span class="bokeh" style="left:360px;top:20px;width:90px;height:90px"></span>
  <span class="bokeh" style="left:690px;top:0;width:110px;height:110px"></span>
  <span class="bokeh" style="left:280px;top:330px;width:70px;height:70px"></span>
  <span class="bokeh" style="left:760px;top:120px;width:60px;height:60px"></span>
  <span class="bokeh" style="left:820px;top:610px;width:70px;height:70px"></span>

  <div class="hero-photo" role="img" aria-label="Photo of a fit woman in a grey sports top and shorts holding dumbbells"></div>

  <div class="brand-box"><span class="brand-name">Clara Vantrell</span></div>
  <p class="presents">presents the</p>

  <h1 class="headline">Get<br>Summer<br>ready</h1>

  <p class="intro">with her very own personalised programming to get you ultimate beach body- ready before Summer hits!</p>

  <div class="price-badge">
    <span class="only">ONLY</span>
    <span class="amount">$59.95</span>
    <span class="per">per week</span>
  </div>

  <section class="includes">
    <h2>Includes:</h2>
    <ul>
      <li>Customised meal plan (usually $220)</li>
      <li>Weekly weigh in/check ins with Clara!</li>
      <li>3 weekly training sessions, with different training style to ensure your body is always left guessing, in a fun team environment. Run by one of Clara's very own trainers, from Keep the pace training facility!</li>
      <li>Discounted additional PT sessions.</li>
      <li>Qualified, experienced and result driven trainers</li>
      <li>Proven results with thousands of women, worldwide</li>
      <li>Prize pack for the challenge winner</li>
      <li>The best beach body ready for Summer!</li>
    </ul>
  </section>

  <svg class="footer-band" viewBox="0 0 849 170" preserveAspectRatio="none" aria-hidden="true">
    <path d="M0 20 Q 300 -10 520 20 T 849 18 L849 170 L0 170 Z" fill="#ec77ae"/>
    <path d="M0 34 Q 320 6 540 36 T 849 30 L849 170 L0 170 Z" fill="var(--band-pink)"/>
  </svg>

  <div class="start-badge">
    <div class="start-badge-inner"><span>STARTING<br><strong>SEPTEMBER!!</strong></span></div>
  </div>

  <div class="footer-text">
    <p class="footer-cta">SECURE YOUR PLACE NOW AS PLACES ARE CAPPED:<br>contact@claravantrell.com.au or text <strong>0491 503 617</strong> to sign up NOW</p>
    <p class="terms">t&amp;c -Full 12 weeks must be paid for, even if sessions are missed or cancelled. Weekly deductions must be set up upon confirmation using a credit card, with the first 2 weeks deducted up front, the remaining 10 weeks will be deducted weekly.</p>
  </div>
</div>
</body>
</html>
```